Heron Property Inspection business card

I am the principal inspector of Heron Property Inspections. I serve Northern Virginia from Winchester to Arlington.Associate, Federated Guild of Dwelling Examiners (FGDE)Graduate, FGDE Home Inspectors CourseNational Association of Home Inspectors ExamI'd like the business card to look more professional than comical.I pulled the attached picture off the web. I'd like to have something like that or an image of a house as my logo on the cards.

Target Market(s)

Persons who recently purchased a home.

Industry/Entity Type

Business

Contact Information for Business Card

Bob AllenBadger Home Inspections, LLC.4455 River RoadBluemont, Virginia 20135cell: 703-231-6680e-mail: tkmarlow@postvale.net

Font styles to use
Serif
Sans Serif

Requirements
Must have
• I'd like to have a logo, something that identifies me as a home inspector. The attached images are something that I'd like to have incorporated into my business card logo.
Nice to have
• I'd like a sketch of a house and/or a magnifying glass showing a house being inspected. The attached images are used as a suggestion only, I do not own the images.
Should not have
• Gimmicky stuff. I want to appear professional and trustworthy.

```html
<!DOCTYPE html>
<html lang="en">
<head>
<meta charset="utf-8">
<title>Heron Property Inspections – Business Card</title>
<link href="https://fonts.googleapis.com/css2?family=Cinzel:wght@500&family=Tinos:wght@400;700&display=swap" rel="stylesheet">
<style>
  :root {
    --page-bg: #d9d6d1;
    --card-top: #ffffff;
    --card-bottom: #e3e3e6;
    --brand-blue: #1f3f8f;
    --swoosh-blue: #1d3d8c;
    --text-grey: #555a60;
    --house-light: #d8d2c2;
    --house-dark: #4a4639;
  }
  * { margin: 0; padding: 0; box-sizing: border-box; }
  html, body {
    width: 1200px;
    height: 892px;
    overflow: hidden;
    background: var(--page-bg);
  }
  .business-card {
    position: absolute;
    left: 100px;
    top: 146px;
    width: 1000px;
    height: 600px;
    background: linear-gradient(165deg, var(--card-top) 0%, var(--card-top) 40%, var(--card-bottom) 100%);
    box-shadow: 0 10px 30px rgba(0,0,0,0.18);
    overflow: hidden;
    font-family: "Tinos", "Times New Roman", serif;
  }
  .card-art {
    position: absolute;
    inset: 0;
  }
  .brand {
    position: absolute;
    left: 60px;
    top: 252px;
    display: flex;
    align-items: center;
    gap: 16px;
  }
  .brand-dot {
    width: 50px;
    height: 50px;
    border-radius: 50%;
    background: var(--brand-blue);
    flex: none;
  }
  .brand-name {
    font-family: "Cinzel", "Times New Roman", serif;
    font-weight: 500;
    color: var(--brand-blue);
    line-height: 1.1;
  }
  .brand-name .line-main { display: block; font-size: 34px; letter-spacing: 0.5px; }
  .brand-name .line-sub  { display: block; font-size: 24px; letter-spacing: 0.5px; }
  .person {
    position: absolute;
    left: 126px;
    top: 356px;
  }
  .person-name {
    font-weight: 700;
    font-size: 44px;
    color: var(--brand-blue);
    line-height: 1;
  }
  .person-title {
    margin-top: 6px;
    font-size: 20px;
    color: var(--text-grey);
  }
  .contact-list {
    position: absolute;
    left: 134px;
    top: 454px;
    list-style: none;
  }
  .contact-item {
    display: flex;
    align-items: center;
    gap: 16px;
    height: 42px;
    font-size: 28px;
    color: var(--text-grey);
  }
  .contact-icon {
    width: 22px;
    height: 22px;
    flex: none;
  }
</style>
</head>
<body>
  <div class="business-card">
    <svg class="card-art" width="1000" height="600" viewBox="0 0 1000 600">
      <defs>
        <clipPath id="upper-region">
          <path d="M345 0 C 430 220, 640 284, 1000 142 L1000 0 Z"/>
        </clipPath>
        <linearGradient id="house-tones" x1="0" y1="0" x2="1" y2="1">
          <stop offset="0" stop-color="var(--house-dark)"/>
          <stop offset="0.5" stop-color="var(--house-light)"/>
          <stop offset="1" stop-color="var(--house-dark)"/>
        </linearGradient>
      </defs>
      <rect class="house-illustration" x="600" y="24" width="340" height="270" rx="6"
            fill="url(#house-tones)" clip-path="url(#upper-region)"
            role="img" aria-label="Illustration of a two-storey house examined under a magnifying glass"/>
      <path class="swoosh" fill="var(--swoosh-blue)"
            d="M320 0 C 415 238, 640 306, 1000 152 L1000 142 C 640 284, 430 220, 345 0 Z"/>
    </svg>

    <div class="brand">
      <span class="brand-dot"></span>
      <div class="brand-name">
        <span class="line-main">Tim Marlow Heron</span>
        <span class="line-sub">Property Inspections, LLC</span>
      </div>
    </div>

    <div class="person">
      <div class="person-name">Employee name</div>
      <div class="person-title">Managing Director</div>
    </div>

    <ul class="contact-list">
      <li class="contact-item">
        <svg class="contact-icon" viewBox="0 0 24 24" aria-hidden="true">
          <rect width="24" height="24" rx="5" fill="var(--brand-blue)"/>
          <rect x="8" y="5" width="8" height="14" rx="1.5" fill="none" stroke="#fff" stroke-width="1.8"/>
        </svg>
        <span>703-555-0192</span>
      </li>
      <li class="contact-item">
        <svg class="contact-icon" viewBox="0 0 24 24" aria-hidden="true">
          <rect width="24" height="24" rx="5" fill="var(--brand-blue)"/>
          <rect x="5" y="7" width="14" height="10" fill="none" stroke="#fff" stroke-width="1.6"/>
          <path d="M5 7 L12 13 L19 7" fill="none" stroke="#fff" stroke-width="1.6"/>
        </svg>
        <span>tkmarlow@postvale.net</span>
      </li>
      <li class="contact-item">
        <svg class="contact-icon" viewBox="0 0 24 24" aria-hidden="true">
          <rect width="24" height="24" rx="5" fill="var(--brand-blue)"/>
          <path d="M12 19 C 8 14, 7 12, 7 10 A5 5 0 0 1 17 10 C 17 12, 16 14, 12 19 Z" fill="#fff"/>
          <circle cx="12" cy="10" r="2" fill="var(--brand-blue)"/>
        </svg>
        <span>7182 Quarry Lane Fernhill, Virginia 20148</span>
      </li>
    </ul>
  </div>
</body>
</html>
```